Velk Partners Building Business Cards

We need a business card that reflects our business as "Solar Experts" in San Diego. Browse our website www.velkpartners.example our License needs to be displayed as "CSLB# 3867140" our phone number is (619) 555-0187

Save thousands on your electric bills and increase the value of your home while helping to protect the environment. Our solar installation experts will help you design the system that's right for you, using only the highest quality equipment that will look great and give you ideal performance. Our goal is to make you energy independent, and get your electric bill to 0.

Paul Osterby
(619) 555-0187
paul@velkpartners.example

Target Market(s)

Home owners in san diego looking for solar

Industry/Entity Type

Solar Energy

Contact Information for Business Card

Paul Osterby
(619) 555-0187
paul@velkpartners.example

Font styles to use
Other font styles liked:
• Use our logo font

Requirements
Must have
• License needs to be displayed as "CSLB# 3867140" our phone number is (619) 555-0187
Nice to have
• Real images of rooftop home solar in san diego
Should not have
• our business address

```html
<!DOCTYPE html>
<html lang="en">
<head>
<meta charset="utf-8">
<title>Velk Partners Building – Business Card</title>
<link rel="stylesheet" href="https://fonts.googleapis.com/css2?family=Oswald:wght@500&family=Open+Sans:wght@400;600;700&display=swap">
<style>
  :root {
    --navy: #1a4a82;
    --orange: #f5a91f;
    --ink: #333b44;
    --paper: #ffffff;
    --backdrop: #e6e4e1;
  }
  * { box-sizing: border-box; margin: 0; padding: 0; }
  html, body { width: 1200px; height: 1000px; overflow: hidden; }
  body {
    position: relative;
    background: var(--backdrop);
    font-family: "Open Sans", Arial, sans-serif;
    color: var(--ink);
  }
  .card {
    position: absolute;
    left: 316px;
    width: 562px;
    height: 320px;
    border-radius: 22px;
    box-shadow: 0 4px 10px rgba(0,0,0,0.22);
  }
  .card-front { top: 171px; background: var(--paper); }
  .card-back { top: 535px; background: var(--navy); }

  .brand-front {
    position: absolute;
    right: 24px;
    top: 42px;
    text-align: right;
    color: var(--navy);
    font-weight: 700;
    line-height: 1.05;
  }
  .brand-front .brand-main { font-size: 27px; letter-spacing: -0.5px; }
  .brand-front .brand-sub { font-size: 15px; letter-spacing: 1px; }

  .holder-name {
    position: absolute;
    left: 37px;
    top: 140px;
    font-family: "Oswald", "Arial Narrow", sans-serif;
    font-weight: 500;
    font-size: 25px;
    letter-spacing: 0.3px;
    color: var(--navy);
  }
  .holder-name .surname { color: var(--orange); }
  .name-rule {
    position: absolute;
    left: 37px;
    top: 190px;
    width: 68px;
    height: 2px;
    background: var(--navy);
  }
  .contact-list {
    position: absolute;
    left: 36px;
    top: 217px;
    list-style: none;
    font-size: 14px;
    line-height: 21px;
    color: var(--ink);
  }
  .contact-list li { display: flex; align-items: center; gap: 10px; }
  .contact-list svg { width: 12px; height: 12px; flex: none; }
  .domain { color: var(--orange); }
  .license {
    position: absolute;
    right: 36px;
    top: 260px;
    font-size: 12px;
    font-weight: 600;
    color: #1d2126;
  }

  .brand-back {
    position: absolute;
    left: 0;
    right: 0;
    top: 112px;
    text-align: center;
    color: #ffffff;
    font-weight: 700;
    line-height: 1.05;
  }
  .brand-back .brand-main { font-size: 54px; letter-spacing: -1px; }
  .brand-back .brand-sub { font-size: 30px; letter-spacing: 1px; margin-top: 4px; }
  .web-back {
    position: absolute;
    left: 0;
    right: 0;
    top: 270px;
    text-align: center;
    font-size: 14px;
    color: #ffffff;
    letter-spacing: 0.3px;
  }
</style>
</head>
<body>
  <section class="card card-front" aria-label="Card front">
    <div class="brand-front">
      <div class="brand-main">Velk Partners</div>
      <div class="brand-sub">Building Inc</div>
    </div>

    <h1 class="holder-name">PAUL <span class="surname">OSTERBY</span></h1>
    <div class="name-rule"></div>

    <ul class="contact-list">
      <li>
        <svg viewBox="0 0 12 12" aria-hidden="true"><rect x="3" y="0.5" width="6" height="11" rx="1.2" fill="none" stroke="#1a4a82" stroke-width="1.2"/><line x1="5" y1="9.6" x2="7" y2="9.6" stroke="#1a4a82" stroke-width="1"/></svg>
        <span>(619) 555-0187</span>
      </li>
      <li>
        <svg viewBox="0 0 12 12" aria-hidden="true"><rect x="0.6" y="2" width="10.8" height="8" fill="none" stroke="#1a4a82" stroke-width="1.1"/><polyline points="0.8,2.4 6,6.6 11.2,2.4" fill="none" stroke="#1a4a82" stroke-width="1.1"/></svg>
        <span>paul@velkpartners.example</span>
      </li>
      <li>
        <svg viewBox="0 0 12 12" aria-hidden="true"><circle cx="6" cy="6" r="5.3" fill="none" stroke="#1a4a82" stroke-width="1.1"/><ellipse cx="6" cy="6" rx="2.3" ry="5.3" fill="none" stroke="#1a4a82" stroke-width="1"/><line x1="0.7" y1="6" x2="11.3" y2="6" stroke="#1a4a82" stroke-width="1"/></svg>
        <span>www.<span class="domain">velkpartners</span>.example</span>
      </li>
    </ul>

    <p class="license">License-"CSLB# 3867140"</p>
  </section>

  <section class="card card-back" aria-label="Card back">
    <div class="brand-back">
      <div class="brand-main">Velk Partners</div>
      <div class="brand-sub">Building Inc</div>
    </div>
    <p class="web-back">www.<span class="domain">velkpartners</span>.example</p>
  </section>
</body>
</html>
```